Business Card Design

New business card design

Target Market(s)

Residential & Commercial Property Managers

Industry/Entity Type

Plumbing Services

Contact Information for Business Card

Name - Rowan Keddle, title - Director, Phone Number - 0431 286 517, email - rowan@tbk-plumbing.com.au, Company ABN - 73 215 904 386,

Font styles to use
Sans Serif

Colors
0054AA
0677BA
7BADD7
CADEEF
E8F1F8

```html
<!DOCTYPE html>
<html lang="en">
<head>
<meta charset="utf-8">
<title>TBK Plumbing Services – Business Card</title>
<link href="https://fonts.googleapis.com/css2?family=Montserrat:wght@400;500;700&display=swap" rel="stylesheet">
<style>
  :root {
    --backdrop: #1b1b1c;
    --card-light: #ffffff;
    --card-dark: #1d222a;
    --ink: #1e2530;
    --ink-soft: #2a2a2a;
    --drop-blue: #2aa3e0;
    --on-dark: #ffffff;
  }
  * { margin: 0; padding: 0; box-sizing: border-box; }
  html, body {
    width: 1200px;
    height: 1059px;
    overflow: hidden;
    background: var(--backdrop);
    font-family: "Montserrat", sans-serif;
  }
  .stage { position: relative; width: 1200px; height: 1059px; }
  .card {
    position: absolute;
    border-radius: 24px;
    box-shadow: 0 10px 24px rgba(0,0,0,0.55);
  }
  .card--front { left: 256px; top: 89px; width: 688px; height: 391px; background: var(--card-light); color: var(--ink); }
  .card--back { left: 253px; top: 546px; width: 694px; height: 395px; background: var(--card-dark); }

  .brand {
    position: absolute;
    left: 0; right: 0;
    display: flex;
    align-items: center;
    justify-content: center;
    gap: 16px;
  }
  .brand__dot { width: 26px; height: 26px; border-radius: 50%; background: var(--drop-blue); flex: none; }
  .brand__name { font-weight: 500; font-size: 40px; letter-spacing: 1px; white-space: nowrap; }
  .card--front .brand { top: 100px; }
  .card--front .brand__name { color: var(--ink); }
  .card--back .brand { top: 165px; }
  .card--back .brand__name { color: var(--on-dark); }

  .person { position: absolute; right: 363px; top: 246px; text-align: right; }
  .person__name { font-weight: 700; font-size: 23px; line-height: 1.1; color: var(--ink); }
  .person__title { font-weight: 400; font-size: 14px; color: var(--ink); margin-top: 2px; }

  .divider { position: absolute; left: 342px; top: 242px; width: 2px; height: 67px; background: var(--ink); }

  .contacts { position: absolute; left: 359px; top: 234px; list-style: none; }
  .contacts__item {
    display: flex; align-items: center; gap: 10px;
    height: 27px; font-size: 14px; font-weight: 400; color: var(--ink-soft);
  }
  .contacts__icon { width: 15px; height: 15px; flex: none; fill: var(--ink); }

  .abn { position: absolute; left: 0; right: 0; top: 345px; text-align: center; font-size: 16px; color: var(--ink-soft); }
  .abn__label { font-weight: 700; }
</style>
</head>
<body>
<main class="stage">
  <section class="card card--front" aria-label="Business card front">
    <div class="brand">
      <span class="brand__dot"></span>
      <span class="brand__name">TBK Plumbing Services</span>
    </div>

    <div class="person">
      <p class="person__name">Rowan Keddle</p>
      <p class="person__title">Director</p>
    </div>

    <div class="divider"></div>

    <ul class="contacts">
      <li class="contacts__item">
        <svg class="contacts__icon" viewBox="0 0 24 24" aria-hidden="true"><path d="M6.6 10.8a15 15 0 0 0 6.6 6.6l2.2-2.2a1 1 0 0 1 1-.25 11.4 11.4 0 0 0 3.6.57 1 1 0 0 1 1 1V20a1 1 0 0 1-1 1A17 17 0 0 1 3 4a1 1 0 0 1 1-1h3.5a1 1 0 0 1 1 1c0 1.25.2 2.45.57 3.6a1 1 0 0 1-.25 1z"/></svg>
        <span>0431 286 517</span>
      </li>
      <li class="contacts__item">
        <svg class="contacts__icon" viewBox="0 0 24 24" aria-hidden="true"><path d="M2 5h20v2l-10 6L2 7z M2 9l10 6 10-6v10H2z"/></svg>
        <span>rowan@tbk-plumbing.com.au</span>
      </li>
      <li class="contacts__item">
        <svg class="contacts__icon" viewBox="0 0 24 24" aria-hidden="true"><path d="M12 2a10 10 0 1 0 0 20 10 10 0 0 0 0-20zm0 2a8 8 0 0 1 6.9 4H15l-2 2 1 3-3 2v3l-2 2A8 8 0 0 1 5 7l3 2 2-2-1-3z"/></svg>
        <span>www.tbk-plumbing.com.au</span>
      </li>
    </ul>

    <p class="abn"><span class="abn__label">ABN</span> - 73 215 904 386</p>
  </section>

  <section class="card card--back" aria-label="Business card back">
    <div class="brand">
      <span class="brand__dot"></span>
      <span class="brand__name">TBK Plumbing Services</span>
    </div>
  </section>
</main>
</body>
</html>
```